Local Roofing/Construction company business needs new biz card design

We need a new business card design, current cards are from the start of this operation and generic at best. We are a local Construction Company (General Contractor) with a majority of our work originating from insurance claims-exterior finish work is the main focus (Roofs-Siding-Gutters etc). Heavily involved with homeowners and the low ball offers they receive from insurance company's after a insurable event takes place. I have attached some of our original logo file(s) below.

```html
<!DOCTYPE html>
<html lang="en">
<head>
<meta charset="utf-8">
<title>Stonecrest Build – Business Card</title>
<link href="https://fonts.googleapis.com/css2?family=Open+Sans:wght@400;600;700;800&display=swap" rel="stylesheet">
<style>
  :root {
    --stage: #1c1c1f;
    --card: #0a1c1e;
    --card-deep: #061315;
    --green: #4cbe6c;
    --white: #ffffff;
    --faint: #123029;
    --pattern-top: #3a4446;
  }
  * { box-sizing: border-box; margin: 0; padding: 0; }
  html, body {
    width: 1200px; height: 780px; overflow: hidden;
    background: var(--stage);
    font-family: "Open Sans", sans-serif;
  }
  .canvas { position: relative; width: 1200px; height: 780px; }

  .card {
    position: absolute; top: 235px;
    width: 540px; height: 310px;
    background: var(--card);
    border: 3px solid var(--green);
    border-radius: 22px;
    overflow: hidden;
  }
  .card--front { left: 40px; }
  .card--back { left: 620px; }

  /* front side */
  .pattern-field {
    position: absolute; inset: 0;
    background: linear-gradient(200deg, var(--pattern-top) 0%, var(--card) 45%, var(--card-deep) 100%);
  }
  .badge {
    position: absolute;
    display: flex; align-items: center; gap: 8px;
    background: var(--green);
    color: var(--white);
    font-weight: 800;
    text-transform: uppercase;
    border-radius: 6px;
    white-space: nowrap;
  }
  .badge__square { background: var(--card); display: block; }
  .card--front .badge {
    right: 28px; top: 150px;
    padding: 6px 12px; font-size: 13px; letter-spacing: .5px;
  }
  .card--front .badge__square { width: 12px; height: 12px; }

  /* back side */
  .mark-shadow {
    position: absolute; right: 40px; top: 40px;
    width: 190px; height: 190px;
    background: var(--faint);
    border-radius: 10px;
  }
  .card--back .badge {
    left: 26px; top: 26px;
    padding: 10px 16px; font-size: 20px; letter-spacing: 1px;
  }
  .card--back .badge__square { width: 18px; height: 18px; }

  .contact { position: absolute; left: 30px; top: 92px; color: var(--white); }
  .contact__name { color: var(--green); font-size: 22px; font-weight: 700; line-height: 1.1; }
  .contact__title { font-size: 12px; font-weight: 600; margin-bottom: 10px; }
  .contact__address { font-size: 11px; line-height: 1.35; margin-bottom: 10px; }
  .contact__list { list-style: none; font-size: 11px; line-height: 1.55; }
  .contact__list li { display: flex; align-items: center; gap: 8px; }
  .contact__list svg { width: 11px; height: 11px; fill: var(--green); flex: none; }

  .signature { position: absolute; right: 0; top: 68px; display: flex; align-items: stretch; }
  .signature__text { text-align: right; padding-right: 12px; padding-top: 2px; }
  .signature__name { font-size: 20px; font-weight: 700; color: var(--green); line-height: 1.1; }
  .signature__name span { color: var(--white); }
  .signature__title { font-size: 11px; font-weight: 600; color: var(--white); }
  .signature__bar { width: 22px; background: var(--green); }
</style>
</head>
<body>
<main class="canvas">

  <section class="card card--front" aria-label="Card front">
    <div class="pattern-field" role="img" aria-label="Repeating brand mark pattern fading from grey at the top to dark teal"></div>
    <div class="badge"><span class="badge__square"></span>Stonecrest Build</div>
  </section>

  <section class="card card--back" aria-label="Card back">
    <div class="mark-shadow" aria-hidden="true"></div>

    <div class="badge"><span class="badge__square"></span>Stonecrest Build</div>

    <div class="signature">
      <div class="signature__text">
        <p class="signature__name">Marta <span>Holloway</span></p>
        <p class="signature__title">Managing Director</p>
      </div>
      <div class="signature__bar"></div>
    </div>

    <div class="contact">
      <p class="contact__name">Marta Holloway</p>
      <p class="contact__title">Co-Founder</p>
      <p class="contact__address">245 Cedar Hollow<br>Rd, Lakeview, MO 63012</p>
      <ul class="contact__list">
        <li><svg viewBox="0 0 24 24"><path d="M6.6 10.8a15 15 0 0 0 6.6 6.6l2.2-2.2a1 1 0 0 1 1-.25 11.4 11.4 0 0 0 3.6.57 1 1 0 0 1 1 1V20a1 1 0 0 1-1 1A17 17 0 0 1 3 4a1 1 0 0 1 1-1h3.5a1 1 0 0 1 1 1c0 1.25.2 2.45.57 3.57a1 1 0 0 1-.25 1z"/></svg>555-201-3344</li>
        <li><svg viewBox="0 0 24 24"><path d="M6.6 10.8a15 15 0 0 0 6.6 6.6l2.2-2.2a1 1 0 0 1 1-.25 11.4 11.4 0 0 0 3.6.57 1 1 0 0 1 1 1V20a1 1 0 0 1-1 1A17 17 0 0 1 3 4a1 1 0 0 1 1-1h3.5a1 1 0 0 1 1 1c0 1.25.2 2.45.57 3.57a1 1 0 0 1-.25 1z"/></svg>555-201-7788 (Emergency)</li>
        <li><svg viewBox="0 0 24 24"><path d="M12 2a10 10 0 1 0 0 20 10 10 0 0 0 0-20zm6.9 6h-3a15.7 15.7 0 0 0-1.4-3.6A8 8 0 0 1 18.9 8zM12 4c.8 1.2 1.5 2.5 1.9 4h-3.8c.4-1.5 1.1-2.8 1.9-4zM4.3 14a8.2 8.2 0 0 1 0-4h3.4a16 16 0 0 0 0 4zm.8 2h3a15.7 15.7 0 0 0 1.4 3.6A8 8 0 0 1 5.1 16zm3-8h-3a8 8 0 0 1 4.3-3.6A15.7 15.7 0 0 0 8.1 8zM12 20c-.8-1.2-1.5-2.5-1.9-4h3.8c-.4 1.5-1.1 2.8-1.9 4zm2.3-6H9.7a14.7 14.7 0 0 1 0-4h4.6a14.7 14.7 0 0 1 0 4zm.3 5.6a15.7 15.7 0 0 0 1.4-3.6h3a8 8 0 0 1-4.4 3.6zm1.7-5.6a16 16 0 0 0 0-4h3.4a8.2 8.2 0 0 1 0 4z"/></svg>www.stonecrestbuild.com</li>
        <li><svg viewBox="0 0 24 24"><path d="M20 4H4a2 2 0 0 0-2 2v12a2 2 0 0 0 2 2h16a2 2 0 0 0 2-2V6a2 2 0 0 0-2-2zm0 4-8 5-8-5V6l8 5 8-5z"/></svg>office@stonecrestbuild.com</li>
      </ul>
    </div>
  </section>

</main>
</body>
</html>
```